Business card design

I am open to ideas. I was thinking of a vertical design, turning the name 90 degrees and placing it on the left edge, then some clipped portion of the fabulous tree with contact info on the bottom -- special emphasis on Web address:WhimBeads.comFor All Your Beading Needs121 E. Cotati AveCotati, CA 94931(707) 664-8343

```html
<!DOCTYPE html>
<html lang="en">
<head>
<meta charset="utf-8">
<title>Fern &amp; Glass — Business Card</title>
<link rel="stylesheet" href="https://fonts.googleapis.com/css2?family=Roboto:wght@300;400;700&display=swap">
<style>
  :root {
    --backdrop: #1c1c1c;
    --card: #121212;
    --card-edge: #1a1a1a;
    --ink: #f2f2f2;
    --ink-soft: #d6d6d6;
    --rule: #5a5a5a;
  }
  * { box-sizing: border-box; margin: 0; padding: 0; }
  html, body {
    width: 1200px; height: 900px; overflow: hidden;
    background: var(--backdrop);
    font-family: "Roboto", Arial, sans-serif;
    color: var(--ink);
  }
  .stage {
    width: 1200px; height: 900px;
    display: flex; flex-direction: column;
    align-items: center; justify-content: center; gap: 40px;
  }
  .card {
    width: 580px; height: 340px;
    background: var(--card);
    border: 1px solid var(--card-edge);
    border-radius: 22px;
    box-shadow: 0 14px 34px rgba(0,0,0,.55);
    display: flex; flex-direction: column;
    align-items: center; justify-content: center;
  }
  .brand-mark {
    display: flex; align-items: center; gap: 14px;
  }
  .brand-dot {
    width: 18px; height: 18px; border-radius: 50%;
    background: var(--ink);
  }
  .brand-name {
    font-weight: 300; font-size: 44px; letter-spacing: 1px;
    color: var(--ink);
  }
  .tagline {
    margin-top: 14px;
    font-weight: 400; font-size: 13px; letter-spacing: 2px;
    text-transform: uppercase; color: var(--ink-soft);
  }
  .card-back .brand-name { font-size: 34px; margin-bottom: 10px; }
  .contact-divider {
    display: flex; align-items: center; gap: 12px;
    margin: 8px 0;
  }
  .contact-divider .rule {
    width: 90px; height: 1px; background: var(--rule);
  }
  .contact-icon { width: 26px; height: 26px; }
  .contact-phone { font-weight: 700; font-size: 22px; color: var(--ink-soft); }
  .contact-web { font-weight: 700; font-size: 24px; }
  .contact-address { font-weight: 400; font-size: 18px; }
</style>
</head>
<body>
<main class="stage">
  <section class="card card-front" aria-label="Card front">
    <div class="brand-mark">
      <span class="brand-dot"></span>
      <span class="brand-name">Fern &amp; Glass</span>
    </div>
    <p class="tagline">For all your beading needs</p>
  </section>

  <section class="card card-back" aria-label="Card back">
    <span class="brand-name">Fern &amp; Glass</span>

    <div class="contact-divider">
      <span class="rule"></span>
      <svg class="contact-icon" viewBox="0 0 26 26" aria-hidden="true">
        <circle cx="13" cy="13" r="11.5" fill="none" stroke="currentColor" stroke-width="1.8"/>
        <path d="M9.2 7.5l2 .2 1 2.6-1.3 1.2c.7 1.5 1.9 2.7 3.4 3.4l1.2-1.3 2.6 1 .2 2c-.4.8-1.3 1.3-2.2 1.2-4.1-.4-7.3-3.6-7.7-7.7-.1-.9.4-1.8 1.2-2.2z" fill="currentColor"/>
      </svg>
      <span class="rule"></span>
    </div>
    <p class="contact-phone">(707) 555-0192</p>

    <div class="contact-divider">
      <span class="rule"></span>
      <svg class="contact-icon" viewBox="0 0 26 26" aria-hidden="true">
        <circle cx="13" cy="13" r="11.5" fill="none" stroke="currentColor" stroke-width="1.8"/>
        <circle cx="13" cy="13" r="6" fill="none" stroke="currentColor" stroke-width="1.5"/>
        <path d="M7 13h12M13 7c-2 2-2 10 0 12M13 7c2 2 2 10 0 12" fill="none" stroke="currentColor" stroke-width="1.2"/>
      </svg>
      <span class="rule"></span>
    </div>
    <p class="contact-web">www.FernGlassco.com</p>

    <div class="contact-divider">
      <span class="rule"></span>
      <svg class="contact-icon" viewBox="0 0 26 26" aria-hidden="true">
        <circle cx="13" cy="13" r="11.5" fill="none" stroke="currentColor" stroke-width="1.8"/>
        <path d="M13 19.5s-4.5-4.6-4.5-7.8a4.5 4.5 0 0 1 9 0c0 3.2-4.5 7.8-4.5 7.8z" fill="none" stroke="currentColor" stroke-width="1.6"/>
        <circle cx="13" cy="11.7" r="1.6" fill="currentColor"/>
      </svg>
      <span class="rule"></span>
    </div>
    <p class="contact-address">348 W. Brindle Ave Larkmoor, CA 94977</p>
  </section>
</main>
</body>
</html>
```